Bring me business with this creative business card

Design my new business card. I am looking for something different with an impact. People will take a look at this card & they will 1- see how different & creative I am, 2-understand what I do 3- Call me to meet me!

I make videos with a message, testimonials. I am dynamic, fun, creative & human. My new website is in construction but in the meantime you can check this old one: brightpath.ca & another one Tidebloom.com & tidebloom facebook page.
I make videos. sometimes with a cameraman, sometimes with my phone. As an ex Public Relations agent, the message is the most important thing for me. I want to make my clients shine! When they start with me they often remind me of a lamb, when I finish coaching them they are powerful like LIONS! That's why I need a powerful business card!

Target Market(s)

Entrepreneurs, solo entrepreneurs, small & medium companies & start ups. People i will meet while networking. People that need videos on their website & social Networks to get attention, to be visible. men & women. From 35 to 49 years old.
I am an ex Public relations agent. I used to send clients in traditional medias, now with videos they have more chances to be seen on google the new media. I do videos of the president, his team, his loyal clients saying how great the company is & expert videos like series so people can be seen for example every 1 st of every month with a short 2 minute video. Also with my 20 years in marketing & communications I can coach & give tips to anybody who needs it.
Target: anybody who would like my old website brightpath.ca & I also have another website but it will be off line soon: tidebloom.com could give you ideas.

Industry/Entity Type

Communications

Contact Information for Business Card

I am in Montreal,So the business cards have to be the usual size like we have in Montreal: 9 cm x 5 cm
Details:My text: Mathilde Tessier Communication coach/Lead Storyteller. "Short films that speak for you" off: 514-555-0147 cell: 514-555-0183. tidebloom.com
mathilde@tidebloom.com logo facebook, youtube, instagram

Colors
f37122

Requirements
Must have
• Dynamic, happy. Orange. Be creative in the look but NOT the shape of the card. Easy to read. Big enough to read.
Should not have
• No funny shapes: no round, no square, just the usual. I love creative but NOT on shape.

```html
<!DOCTYPE html>
<html lang="en">
<head>
<meta charset="utf-8">
<title>Tidebloom Business Card</title>
<link href="https://fonts.googleapis.com/css2?family=Roboto:wght@400;500&family=Roboto+Condensed:wght@500&display=swap" rel="stylesheet">
<style>
  :root {
    --backdrop: #2a2a2a;
    --paper: #f4f4f3;
    --orange: #e25a21;
    --orange-deep: #e8531f;
    --amber: #f0a020;
    --ink: #444444;
    --rule: #c9c9c9;
    --white: #ffffff;
  }
  * { margin: 0; padding: 0; box-sizing: border-box; }
  html, body { width: 1200px; height: 960px; overflow: hidden; }
  body {
    background: var(--backdrop);
    position: relative;
    font-family: "Roboto", Arial, sans-serif;
  }
  .card {
    position: absolute;
    width: 600px;
    height: 342px;
    overflow: hidden;
  }
  .card--front { left: 314px; top: 113px; background: var(--paper); }
  .card--back { left: 311px; top: 472px; background: var(--orange); }

  /* Brand lockup: plain circle above the name */
  .brand-mark {
    position: absolute;
    border-radius: 50%;
  }
  .brand-name {
    position: absolute;
    left: 0; width: 100%;
    text-align: center;
    font-family: "Roboto", Arial, sans-serif;
    font-weight: 500;
    letter-spacing: 1px;
    line-height: 1;
  }

  /* Front */
  .card--front .brand-mark {
    left: 127px; top: 100px; width: 88px; height: 88px;
    background: var(--orange);
  }
  .card--front .brand-block {
    position: absolute; left: 81px; top: 204px; width: 180px; height: 36px;
  }
  .card--front .brand-name { top: 0; font-size: 30px; color: var(--orange); }

  .divider {
    position: absolute; left: 283px; top: 85px; width: 1px; height: 175px;
    background: linear-gradient(to bottom, transparent, var(--rule) 20%, #9a9a9a 50%, var(--rule) 80%, transparent);
  }
  .identity { position: absolute; left: 309px; top: 94px; }
  .identity__name {
    font-family: "Roboto Condensed", "Arial Narrow", sans-serif;
    font-weight: 500; font-size: 23px; color: var(--orange-deep); letter-spacing: 0.5px;
    line-height: 28px;
  }
  .identity__role {
    font-size: 15px; color: var(--amber); line-height: 19px; margin-top: 3px;
  }
  .contacts { position: absolute; left: 309px; top: 174px; list-style: none; }
  .contacts li {
    display: flex; align-items: center; gap: 9px;
    font-size: 14px; color: var(--ink); height: 19px;
  }
  .contacts svg { width: 13px; height: 13px; fill: var(--orange-deep); flex: none; }

  .footer-band {
    position: absolute; left: 0; bottom: 0; width: 600px; height: 14px;
  }

  /* Back */
  .card--back .brand-mark {
    left: 250px; top: 60px; width: 100px; height: 100px;
    background: #f39a1e;
  }
  .card--back .brand-block { position: absolute; left: 150px; top: 200px; width: 300px; height: 36px; }
  .card--back .brand-name { top: 0; font-size: 34px; color: var(--white); }
  .slogan {
    position: absolute; top: 254px; left: 0; width: 100%;
    text-align: center; color: var(--white); font-size: 14px; font-weight: 500;
  }
  .social-row {
    position: absolute; top: 297px; left: 170px; width: 260px; height: 24px;
    display: flex; align-items: center; justify-content: center; gap: 5px;
  }
  .social-row::before, .social-row::after {
    content: ""; display: block; flex: 1; height: 1px;
  }
  .social-row::before { background: linear-gradient(to right, transparent, rgba(255,255,255,0.8)); margin-right: 4px; }
  .social-row::after { background: linear-gradient(to left, transparent, rgba(255,255,255,0.8)); margin-left: 4px; }
  .social-dot {
    width: 22px; height: 22px; border-radius: 50%;
    background: var(--white);
  }
</style>
</head>
<body>

  <section class="card card--front" aria-label="Business card front">
    <div class="brand-mark" aria-hidden="true"></div>
    <div class="brand-block">
      <div class="brand-name">TIDEBLOOM</div>
    </div>

    <div class="divider"></div>

    <div class="identity">
      <h1 class="identity__name">MATHILDE T.</h1>
      <p class="identity__role">COMMUNICATION COACH<br>LEAD STORYTELLER</p>
    </div>

    <ul class="contacts">
      <li>
        <svg viewBox="0 0 24 24"><path d="M6.6 10.8a15.1 15.1 0 0 0 6.6 6.6l2.2-2.2c.3-.3.7-.4 1-.2 1.1.4 2.3.6 3.6.6.6 0 1 .4 1 1V20c0 .6-.4 1-1 1A17 17 0 0 1 3 4c0-.6.4-1 1-1h3.5c.6 0 1 .4 1 1 0 1.3.2 2.5.6 3.6.1.3 0 .7-.2 1z"/></svg>
        514-555-0147
      </li>
      <li>
        <svg viewBox="0 0 24 24"><path d="M7 1h10a2 2 0 0 1 2 2v18a2 2 0 0 1-2 2H7a2 2 0 0 1-2-2V3a2 2 0 0 1 2-2zm0 3v14h10V4zm5 15.5a1.2 1.2 0 1 0 0 2.4 1.2 1.2 0 0 0 0-2.4z"/></svg>
        514-555-0183.
      </li>
      <li>
        <svg viewBox="0 0 24 24"><path d="M2 5h20v14H2zm2 2v.5l8 5 8-5V7zm0 2.8V17h16V9.8l-8 5z"/></svg>
        mathilde@tidebloom.com
      </li>
      <li>
        <svg viewBox="0 0 24 24"><circle cx="12" cy="12" r="10"/><path d="M7 7c2 0 3 1 3 3s2 2 2 4-1 3-1 4M14 4c0 2 2 2 3 3s0 3 2 4" stroke="#f4f4f3" stroke-width="1.6" fill="none"/></svg>
        www.tidebloom.com
      </li>
    </ul>

    <svg class="footer-band" viewBox="0 0 600 14" preserveAspectRatio="none" aria-hidden="true">
      <polygon points="0,0 392,0 388,14 0,14" fill="#e25a21"/>
      <polygon points="396,0 600,0 600,14 392,14" fill="#f0a020"/>
    </svg>
  </section>

  <section class="card card--back" aria-label="Business card back">
    <div class="brand-mark" aria-hidden="true"></div>
    <div class="brand-block">
      <div class="brand-name">TIDEBLOOM</div>
    </div>
    <p class="slogan">Short films that speak for you</p>
    <div class="social-row" aria-label="Social media links">
      <span class="social-dot"></span>
      <span class="social-dot"></span>
      <span class="social-dot"></span>
    </div>
  </section>

</body>
</html>
```